Redesign website bus travel company Falk Brenz

We require a complete redesign of the website of Reisebüro Falk Brenz, an established bus tour operator based in Graubünden (www.falkbrenz.ch). For years, the company has specialized in multi-day tours throughout Europe, as well as day trips such as shopping trips to Innsbruck or Como, music tours, and market visits, primarily for seniors, as well as car rentals for clubs and companies.

The new website requires a video header with overlay text, red as the primary corporate color, complemented by black and gray, and a highly simplified navigation with two main sections: "Our Trips" and "Bus Rental." The remaining sections must be accessible via the "Menu" menu item. The design should be user-friendly for all age groups and mobile-responsive.

The goal is a trustworthy, modern website that reflects personal service and many years of experience.
The new logo can be found in the files, as well as a few pictures.

Target Market(s)

Guests of bus tours (day and multi-day trips) and bus rentals (clubs, companies, etc.)

Industry/Entity Type

Busreisen und Busvermietung

Number of Pages Required

1 page

Requirements
Must have
• Red as primary color, video header, simple UX for target group seniors
Nice to have
• Photo galleries of destinations and the vehicle fleet

```html
<!DOCTYPE html>
<html lang="en">
<head>
<meta charset="utf-8">
<title>Falk Brenz – Coach Travel</title>
<link rel="stylesheet" href="https://fonts.googleapis.com/css2?family=Poppins:wght@400;500;600;700;800&display=swap">
<style>
:root{
  --red:#c40f14;
  --dark:#262626;
  --black:#111111;
  --white:#ffffff;
  --grey:#eeeeee;
  --text:#222222;
  --muted:#555555;
}
*{margin:0;padding:0;box-sizing:border-box}
html,body{width:1200px;height:3430px;overflow:hidden}
body{font-family:'Poppins',sans-serif;color:var(--text);background:var(--white);position:relative}
a{text-decoration:none}
.abs{position:absolute}
.btn{position:absolute;display:flex;align-items:center;justify-content:center;gap:10px;font-weight:700;font-size:16px;color:var(--white);text-transform:uppercase;letter-spacing:.2px;text-decoration:none}
.btn-red{background:var(--red)}
.btn-dark{background:var(--dark)}
/* header */
.site-header{position:absolute;left:0;top:0;width:1200px;height:83px;background:var(--white)}
.brand{position:absolute;left:76px;top:14px;font-weight:800;font-size:42px;color:var(--red);letter-spacing:-1px}
.call{position:absolute;left:898px;top:22px;display:flex;align-items:center;gap:12px}
.call-icon{width:40px;height:40px;border-radius:50%;background:var(--dark);display:flex;align-items:center;justify-content:center}
.call small{display:block;font-size:11px;font-weight:600;color:var(--red);line-height:1.2}
.call strong{display:block;font-size:19px;font-weight:700;color:var(--black);line-height:1.2}
.main-nav{position:absolute;left:0;top:83px;width:1200px;height:56px;background:var(--red);display:flex;align-items:center;padding-left:60px}
.main-nav a{font-size:13px;font-weight:600;color:var(--white);padding:0 18px;height:56px;display:flex;align-items:center;gap:10px;text-transform:uppercase}
.main-nav a.active{background:var(--black)}
.main-nav .menu-link{margin-left:auto;margin-right:60px}
/* hero */
.hero{position:absolute;left:0;top:139px;width:1200px;height:582px;background:linear-gradient(180deg,#4d5a42 0%,#6b7a55 45%,#5f8a3a 75%,#4a7028 100%)}
.hero::after{content:"";position:absolute;inset:0;background:rgba(0,0,0,.28)}
.hero-content{position:absolute;left:0;top:140px;width:1200px;text-align:center;color:var(--white);z-index:2}
.hero h1{font-size:92px;font-weight:700;line-height:1}
.hero p{font-size:35px;font-weight:700;line-height:1.24;margin-top:14px}
.hero .btn{left:522px;top:341px;width:156px;height:50px;z-index:2}
.play{position:absolute;left:535px;top:405px;display:flex;align-items:center;gap:10px;font-size:16px;font-weight:600;color:var(--white);text-decoration:underline;text-underline-offset:5px;z-index:2}
.arrow{position:absolute;top:268px;z-index:2}
/* trips */
.section-title{position:absolute;left:0;width:1200px;text-align:center;font-size:38px;font-weight:700;color:var(--text)}
.trip-card{position:absolute;top:847px;width:242px;height:304px}
.trip-card .ph{position:absolute;left:0;top:0;width:242px;height:304px}
.trip-card .label{position:absolute;left:0;bottom:0;width:242px;height:75px;background:var(--red);color:var(--white);font-weight:700;font-size:19px;padding:22px 20px;text-transform:uppercase}
.trip-card.active{outline:4px solid var(--red);outline-offset:-4px}
/* about */
.about{position:absolute;left:0;top:1223px;width:1200px;height:433px;background:var(--dark);overflow:hidden}
.about h2{position:absolute;left:75px;top:62px;font-size:38px;font-weight:700;color:var(--white)}
.about h3{position:absolute;left:75px;top:116px;font-size:19px;font-weight:700;color:var(--white)}
.about p{position:absolute;left:75px;top:155px;width:515px;font-size:15px;line-height:27px;color:var(--white)}
.about .btn{left:75px;top:313px;width:157px;height:49px}
.badge{position:absolute;left:947px;top:277px;width:178px;height:156px;background:var(--white);text-align:center;padding-top:10px}
.badge b{display:block;font-size:66px;font-weight:800;color:var(--red);line-height:1}
.badge span{display:block;font-size:22px;font-weight:700;color:var(--dark);line-height:1.15}
/* gallery */
.gal{position:absolute}
.gal.active{outline:4px solid var(--red);outline-offset:-4px}
/* rental */
.rental{position:absolute;left:0;top:2291px;width:1200px;height:433px;background:var(--red);overflow:hidden}
.rental h2{position:absolute;left:675px;top:98px;font-size:38px;font-weight:700;color:var(--white)}
.rental p{position:absolute;left:675px;top:158px;width:430px;font-size:15px;line-height:27px;color:var(--white)}
.rental .btn{left:675px;top:280px;width:158px;height:49px}
/* program */
.program{position:absolute;left:0;top:2724px;width:1200px;height:380px;background:var(--white);overflow:hidden}
.program h2{position:absolute;left:75px;top:56px;font-size:38px;font-weight:700;line-height:40px;color:var(--text)}
.program p{position:absolute;left:75px;top:145px;width:450px;font-size:21px;line-height:30px;color:var(--text)}
.program .btn{left:75px;top:285px;width:211px;height:51px}
/* footer */
.site-footer{position:absolute;left:0;top:3104px;width:1200px;height:326px;background:var(--grey)}
.f-brand{position:absolute;left:76px;top:64px;font-weight:800;font-size:42px;color:var(--red);letter-spacing:-1px}
.f-copy{position:absolute;left:76px;top:133px;font-size:12px;line-height:22px;color:var(--muted)}
.social{position:absolute;left:76px;top:200px;display:flex;gap:20px}
.social span{width:22px;height:22px;border-radius:50%;background:var(--dark)}
.f-head{position:absolute;font-size:15px;font-weight:700;color:var(--red);text-transform:uppercase}
.f-links{position:absolute;list-style:none;font-size:13px;line-height:33.5px;color:var(--muted)}
.partner{position:absolute;left:675px;top:104px;font-size:26px;font-weight:700;color:var(--red)}
.f-addr{position:absolute;left:675px;top:163px;font-size:13px;line-height:22px;color:var(--muted)}
.f-addr b{color:var(--text);font-weight:600}
.f-phone{position:absolute;left:675px;top:236px;font-size:14px;font-weight:700;color:var(--red);display:flex;gap:8px;align-items:center}
.f-hours{position:absolute;left:946px;top:106px;font-size:13px;line-height:24px;color:var(--muted)}
.f-hours .day{margin-bottom:9px}
</style>
</head>
<body>

<header class="site-header">
  <div class="brand">Falk Brenz</div>
  <div class="call">
    <div class="call-icon">
      <svg width="18" height="18" viewBox="0 0 24 24"><path fill="#fff" d="M6.6 10.8a15.1 15.1 0 0 0 6.6 6.6l2.2-2.2c.3-.3.7-.4 1-.2 1.1.4 2.3.6 3.6.6.6 0 1 .4 1 1V20c0 .6-.4 1-1 1A17 17 0 0 1 3 4c0-.6.4-1 1-1h3.5c.6 0 1 .4 1 1 0 1.3.2 2.5.6 3.6.1.3 0 .7-.2 1l-2.3 2.2z"/></svg>
    </div>
    <div><small>CALL TODAY</small><strong>+41(0)81 555 01 20</strong></div>
  </div>
</header>

<nav class="main-nav">
  <a class="active" href="#">Our Trips</a>
  <a href="#">Bus Rental</a>
  <a class="menu-link" href="#">
    <svg width="18" height="14" viewBox="0 0 18 14"><path d="M0 1h18M0 7h18M0 13h18" stroke="#fff" stroke-width="2"/></svg>
    Menu
  </a>
</nav>

<section class="hero" role="img" aria-label="Video header: couple in traditional costume with alphorn and accordion in a meadow beside a tour coach">
  <svg class="arrow" style="left:58px" width="30" height="50" viewBox="0 0 30 50"><path d="M26 4 6 25l20 21" fill="none" stroke="#fff" stroke-width="4"/></svg>
  <svg class="arrow" style="left:1112px" width="30" height="50" viewBox="0 0 30 50"><path d="m4 4 20 21L4 46" fill="none" stroke="#fff" stroke-width="4"/></svg>
  <div class="hero-content">
    <h1>Falk Brenz</h1>
    <p>The Graubünden coach travel agency with<br>13 - 79 seater coaches.</p>
  </div>
  <a class="btn btn-red" href="#">Read More</a>
  <span class="play">
    <svg width="16" height="16" viewBox="0 0 16 16"><circle cx="8" cy="8" r="8" fill="#fff"/><path d="M6 4.5v7l5.5-3.5z" fill="#333"/></svg>
    PLAY-VIDEO
  </span>
</section>

<h2 class="section-title" style="top:780px">OUR TRIPS</h2>

<div class="trip-card" style="left:75px">
  <div class="ph" role="img" aria-label="Double-decker coach parked beside a sunflower field" style="background:linear-gradient(180deg,#6e8f50,#3f6a2c 60%,#c9a526)"></div>
  <div class="label">Day Trips</div>
</div>
<div class="trip-card active" style="left:345px">
  <div class="ph" role="img" aria-label="White sun loungers on a lakeside beach" style="background:linear-gradient(180deg,#8fb6d8,#5a86a8 40%,#d9dcdf)"></div>
  <div class="label">Holiday Trips</div>
</div>
<div class="trip-card" style="left:614px">
  <div class="ph" role="img" aria-label="Group of travellers in green jackets in front of a coach" style="background:linear-gradient(180deg,#6a7480,#5ba53a 50%,#555)"></div>
  <div class="label">Group Tours</div>
</div>
<div class="trip-card" style="left:885px">
  <div class="ph" role="img" aria-label="Blue coach parked near satellite dishes under a blue sky" style="background:linear-gradient(180deg,#2b73c9,#7fb0e0 45%,#3a86d4 70%,#5d8a3a)"></div>
  <div class="label">Airport Transfer</div>
</div>

<section class="about">
  <svg class="abs" style="left:0;top:0" width="1200" height="433" viewBox="0 0 1200 433" role="img" aria-label="The two owners smiling in front of a coach">
    <defs><linearGradient id="aboutPh" x1="0" y1="0" x2="1" y2="1"><stop offset="0" stop-color="#7d8b6a"/><stop offset=".5" stop-color="#3a3a3a"/><stop offset="1" stop-color="#2d6fb8"/></linearGradient></defs>
    <polygon points="706,0 1200,0 1200,433 533,433" fill="url(#aboutPh)"/>
  </svg>
  <h2>ABOUT US</h2>
  <h3>EXPERIENCE THE WORLD WITH US</h3>
  <p>The Falk travel agency has existed for over 60 years and has been run by Marco Seiler and Luca Imhof, the fourth generation of the family, since August 1, 2013. Our travel industry expertise, friendly and reliable service, and competitive prices set us apart from the competition.</p>
  <a class="btn btn-red" href="#">Read More</a>
  <div class="badge"><b>60</b><span>YEARS OF<br>EXPERIENCE</span></div>
</section>

<h2 class="section-title" style="top:1708px">OUR GALLERY</h2>
<div class="gal" role="img" aria-label="Old town with castle towers at sunset" style="left:75px;top:1786px;width:342px;height:208px;background:linear-gradient(180deg,#d89a4a,#a87a4a 50%,#4f6a3a)"></div>
<div class="gal" role="img" aria-label="White coach on a motorway" style="left:75px;top:2007px;width:342px;height:208px;background:linear-gradient(180deg,#bfc3c6,#888d90)"></div>
<div class="gal active" role="img" aria-label="Red, white and blue coach in a mountain meadow" style="left:429px;top:1786px;width:341px;height:429px;background:linear-gradient(180deg,#3f5a3a,#5c7a48 35%,#2f6fc2 55%,#6f9a3a 80%)"></div>
<div class="gal" role="img" aria-label="Roman stone aqueduct over a river" style="left:785px;top:1786px;width:342px;height:208px;background:linear-gradient(180deg,#1f66c8,#c59a55 50%,#3a9a88)"></div>
<div class="gal" role="img" aria-label="Silver coach on a road" style="left:785px;top:2007px;width:342px;height:208px;background:linear-gradient(180deg,#8a8a86,#c9cbcc 60%,#7e8080)"></div>

<section class="rental">
  <svg class="abs" style="left:0;top:0" width="1200" height="433" viewBox="0 0 1200 433" role="img" aria-label="Silver coach parked in front of a building">
    <defs><linearGradient id="rentPh" x1="0" y1="0" x2="0" y2="1"><stop offset="0" stop-color="#b8c8dc"/><stop offset=".5" stop-color="#8e9399"/><stop offset="1" stop-color="#5a5d60"/></linearGradient></defs>
    <polygon points="0,0 493,0 666,433 0,433" fill="url(#rentPh)"/>
  </svg>
  <h2>BUS RENTAL</h2>
  <p>Duis aute irure dolor in reprehenderit in voluptate velit esse cillum dolore eu fugiat nulla pariatur. Excepteur sint occaecat cupidatat non proident, sunt in culpa qui officia deserunt mollit anim id est laborum.</p>
  <a class="btn btn-dark" href="#">Read More</a>
</section>

<section class="program">
  <svg class="abs" style="left:0;top:0" width="1200" height="380" viewBox="0 0 1200 380" role="img" aria-label="Coach parked by palm trees on a sunny square">
    <defs><linearGradient id="progPh" x1="0" y1="0" x2="0" y2="1"><stop offset="0" stop-color="#3a7ad0"/><stop offset=".45" stop-color="#8db6e2"/><stop offset=".7" stop-color="#4d7a32"/><stop offset="1" stop-color="#6f9a3e"/></linearGradient></defs>
    <polygon points="666,0 1200,0 1200,380 523,380" fill="url(#progPh)"/>
  </svg>
  <h2>THE 2025 TRAVEL<br>PROGRAM IS HERE!</h2>
  <p>You can find all tours and day trips online under the "Day Trips" and "Holiday Trips" sections - browse through them, there's something for everyone.</p>
  <a class="btn btn-red" href="#">
    <svg width="14" height="17" viewBox="0 0 14 17"><path d="M0 0h9l5 5v12H0z" fill="#fff"/></svg>
    Download PDF
  </a>
</section>

<footer class="site-footer">
  <div class="f-brand">Falk Brenz</div>
  <div class="f-copy">Copyright © 2025 Company Name<br>All Right Reserved</div>
  <div class="social" aria-label="Social links"><span></span><span></span><span></span><span></span><span></span></div>

  <div class="f-head" style="left:345px;top:71px">Quick Links</div>
  <ul class="f-links" style="left:345px;top:89px"><li>Start</li><li>About Us</li><li>Day Trips</li><li>Holiday Trips</li><li>Group Tours</li><li>Airport Transfer</li></ul>
  <ul class="f-links" style="left:491px;top:89px"><li>Minibus Rental</li><li>The Driver-Making</li><li>Contact</li></ul>

  <div class="partner">Seiler &amp; Imhof</div>
  <div class="f-addr"><b>Travel Agency Falk</b><br>c/o Seiler Imhof Car-Reisen AG<br>Talweg 22 CH-7000 Brenz</div>
  <div class="f-phone">
    <svg width="12" height="12" viewBox="0 0 24 24"><path fill="#c40f14" d="M6.6 10.8a15.1 15.1 0 0 0 6.6 6.6l2.2-2.2c.3-.3.7-.4 1-.2 1.1.4 2.3.6 3.6.6.6 0 1 .4 1 1V20c0 .6-.4 1-1 1A17 17 0 0 1 3 4c0-.6.4-1 1-1h3.5c.6 0 1 .4 1 1 0 1.3.2 2.5.6 3.6.1.3 0 .7-.2 1l-2.3 2.2z"/></svg>
    +41(0)81 555 01 20
  </div>

  <div class="f-head" style="left:946px;top:71px">Hours</div>
  <div class="f-hours"><div class="day">Monday - Friday</div>8:00 a.m. - 12:00 p.m. &amp;<br>1:30 p.m. - 5:00 p.m.</div>
</footer>

</body>
</html>
```